Social Media App Needs PPT Template

We need a PowerPoint template for a new social media company based in the DC area called "Bold Ledger." We provide an interactive digital platform for executives to share actionable advice. We would like to see designs that use our orange logo color as an accent, but are mainly grey, white, and black. The final design should communicate clean, chic, modern, and professional.

Target Market(s)

Executives

Industry/Entity Type

Information Technology

Font styles to use
Sans Serif

Colors
f78f20
fbe7d2
ffffff
000000
e8e8e8
757575

Requirements
Must have
• My project must have title page and many options for the body of the ppt (graphs, tables, etc). It also needs to be easy to modify. I must have someone who is experienced in creating powerpoint templates.
Nice to have
• It would be nice to have a very modern and clean design that includes the logo on every page, but still leaves a lot of room for the content of the slide
Should not have
• My design project should not look to busy.

```html
<!DOCTYPE html>
<html lang="en">
<head>
<meta charset="utf-8">
<title>Bold Ledger – Presentation Template</title>
<link href="https://fonts.googleapis.com/css2?family=Lato:ital,wght@0,300;0,400;0,700;1,400&display=swap" rel="stylesheet">
<style>
  :root{
    --orange:#f78f20;
    --orange-soft:#fbe7d2;
    --white:#ffffff;
    --black:#000000;
    --light:#e8e8e8;
    --mid:#757575;
    --dark:#3b3b3b;
    --paper:#f5f5f5;
    --board:#8c8c8c;
  }
  *{box-sizing:border-box;margin:0;padding:0}
  html,body{width:1200px;height:720px;overflow:hidden;background:var(--board)}
  body{font-family:'Lato',sans-serif;color:var(--mid)}
  .board{
    width:1200px;height:720px;
    display:grid;
    grid-template-columns:repeat(4,262px);
    grid-template-rows:repeat(3,196px);
    column-gap:37px;row-gap:44px;
    padding:32px 0 0 22px;
  }
  .cell{position:relative}
  .page-label{
    position:absolute;top:-21px;left:0;width:100%;
    text-align:center;font-size:7px;color:#d6d6d6;
  }
  .slide{
    position:relative;width:262px;height:196px;overflow:hidden;
    background:var(--paper);
    box-shadow:0 1px 3px rgba(0,0,0,.25);
  }
  .slide > svg.frame{position:absolute;inset:0}
  .slide-title{
    position:absolute;left:8px;top:16px;
    font-size:9px;font-weight:300;color:var(--white);letter-spacing:.1px;
  }
  .brand{
    position:absolute;right:9px;top:18px;
    display:flex;align-items:center;gap:3px;
    font-size:6.5px;font-weight:700;color:var(--white);
  }
  .brand .dot{width:5px;height:5px;border-radius:50%;background:var(--orange)}
  .footer-url{
    position:absolute;left:7px;bottom:4px;font-size:3.3px;color:#bbbbbb;
  }
  .copy{font-size:3.6px;line-height:1.4;color:var(--mid);text-align:justify}
  .copy p+p{margin-top:3px}
  .lead{color:var(--orange);font-style:italic}
  .abs{position:absolute}
  .placeholder{background:#c9c9c9}

  /* title slide */
  .cover .brand-big{
    position:absolute;left:26px;top:58px;
    display:flex;align-items:center;gap:5px;
    font-size:17px;font-weight:700;color:var(--black);
  }
  .cover .brand-big .dot{width:12px;height:12px;border-radius:50%;background:var(--orange)}
  .cover .tagline{
    position:absolute;right:10px;bottom:16px;text-align:right;
    font-size:10px;font-weight:300;line-height:1.35;
  }
  .tagline .accent{color:var(--orange)}
  .tagline .plain{color:var(--white)}

  /* transition slide */
  .transition{background:linear-gradient(160deg,#2c2c2c,#4a4a4a)}
  .transition .image-area{position:absolute;inset:0;display:flex;align-items:center;justify-content:center;padding-bottom:30px}
  .transition .hint{font-size:15px;font-weight:300;color:rgba(255,255,255,.08)}
  .transition .label{position:absolute;right:22px;bottom:18px;font-size:14px;font-weight:300;color:var(--white)}

  /* bullets */
  .bullets{list-style:none;font-size:4.3px;line-height:1.35;color:var(--mid)}
  .bullets li{position:relative;padding-left:7px;margin-bottom:7px}
  .bullets li::before{content:"";position:absolute;left:0;top:1.3px;width:2.5px;height:2.5px;background:var(--orange)}

  /* three column */
  .trio{position:absolute;left:12px;right:12px;top:56px;display:grid;grid-template-columns:repeat(3,1fr);gap:10px}
  .trio .copy{text-align:center}
  .trio svg{display:block;margin:0 auto 10px}

  /* charts */
  .chart{position:absolute;left:8px;top:44px}
  .chart text{font-family:'Lato',sans-serif;font-size:3.6px;fill:var(--mid)}

  /* donut labels */
  .note{position:absolute;width:62px}
  .note h4{font-size:4.2px;font-weight:700;color:var(--dark);margin-bottom:2px}
  .note.hot h4{color:var(--orange)}
  .note.pale h4{color:#b5b5b5}
  .note .copy{text-align:left;font-size:3.3px;color:#9a9a9a}

  /* table */
  .grid-table{position:absolute;left:14px;top:66px;width:236px;border-collapse:collapse;font-size:4px}
  .grid-table th{font-weight:400;color:var(--mid);height:12px;font-size:3.5px;border-bottom:.5px solid #cfcfcf}
  .grid-table td{height:18px;text-align:center;color:var(--dark);font-size:5px}
  .grid-table td:first-child{text-align:left;padding-left:24px;font-size:3.8px}
  .grid-table tr.band td{background:var(--dark);color:var(--white)}

  /* team */
  .team{position:absolute;left:9px;right:9px;top:56px;display:grid;grid-template-columns:repeat(3,1fr);gap:9px}
  .portrait{height:42px;background:linear-gradient(135deg,#d8cfc4,#9aa3ab)}
  .person-name{font-size:4.6px;font-weight:700;color:var(--dark);margin-top:5px}
  .person-role{font-size:3.3px;color:#a0a0a0;margin-bottom:4px}
  .team .copy{text-align:left;font-size:3.3px;border-bottom:.6px solid #bdbdbd;padding-bottom:5px}

  /* stats */
  .stat{position:absolute;width:88px;height:46px;padding:7px 6px 0 22px;color:var(--white)}
  .stat.orange{background:var(--orange)}
  .stat.dark{background:var(--dark)}
  .stat.grey{background:#9d9d9d}
  .stat .figure{font-size:8.5px;font-weight:400;margin-bottom:2px}
  .stat .copy{color:var(--white);text-align:left;font-size:3.3px;line-height:1.3}
  .stat .badge{position:absolute;left:-12px;top:11px;width:24px;height:24px;border-radius:50%;display:flex;align-items:center;justify-content:center}
  .stat.orange .badge{background:var(--orange);border:1.5px solid var(--paper)}
  .stat.dark .badge{background:var(--dark);border:1.5px solid var(--paper)}
  .stat.grey .badge{background:#9d9d9d;border:1.5px solid var(--paper)}

  /* closing */
  .closing{background:var(--orange)}
  .closing .thanks{position:absolute;left:22px;top:26px;font-size:28px;font-weight:300;line-height:1.05;color:var(--white)}
  .closing .site{position:absolute;left:40px;top:120px;font-size:13px;font-weight:300;color:rgba(255,255,255,.18);transform:rotate(-38deg);transform-origin:left top}
  .closing .brand-big{position:absolute;right:14px;bottom:30px;display:flex;align-items:center;gap:4px;font-size:14px;font-weight:700;color:var(--dark)}
  .closing .brand-big .dot{width:9px;height:9px;border-radius:50%;background:var(--dark)}
</style>
</head>
<body>
<main class="board">

  <!-- 1 cover -->
  <section class="cell">
    <div class="page-label">Page 1</div>
    <div class="slide cover">
      <svg class="frame" viewBox="0 0 262 196" width="262" height="196">
        <polygon points="205,0 262,0 262,8 218,42 196,42 236,10 190,10" fill="var(--dark)"/>
        <polygon points="228,24 262,0 262,14 240,30" fill="var(--orange)"/>
        <polygon points="0,196 14,196 262,2 262,-10" fill="var(--orange)" opacity=".95"/>
        <polygon points="18,196 70,196 190,106 138,106" fill="var(--dark)"/>
        <polygon points="58,196 84,196 262,60 262,38" fill="var(--orange)"/>
        <polygon points="88,196 262,196 262,120 186,120" fill="var(--dark)"/>
        <polygon points="0,180 20,166 32,166 8,186 0,186" fill="var(--orange)"/>
      </svg>
      <div class="brand-big"><span class="dot"></span>Bold Ledger</div>
      <div class="tagline">
        <div class="accent">interactive digital platform</div>
        <div class="plain">to share actionable advice</div>
      </div>
    </div>
  </section>

  <!-- 2 transition -->
  <section class="cell">
    <div class="page-label">Page 2</div>
    <div class="slide transition">
      <div class="image-area" role="img" aria-label="Full-bleed section image placeholder"><span class="hint">Image Goes Here</span></div>
      <svg class="frame" viewBox="0 0 262 196" width="262" height="196">
        <polygon points="96,196 262,196 262,154 130,154" fill="#1f1f1f"/>
        <polygon points="76,196 90,196 124,158 110,158" fill="var(--orange)"/>
      </svg>
      <div class="label">Transition Page</div>
    </div>
  </section>

  <!-- 3 text + image -->
  <section class="cell">
    <div class="page-label">Page 3</div>
    <div class="slide">
      <svg class="frame" viewBox="0 0 262 196" width="262" height="196">
        <rect x="0" y="13" width="262" height="22" fill="var(--orange)"/>
        <polygon points="196,10 262,10 262,35 180,35" fill="var(--dark)"/>
        <rect x="0" y="35" width="186" height="1" fill="var(--dark)"/>
        <rect x="0" y="186" width="262" height="10" fill="var(--light)"/>
        <polygon points="70,188 262,188 262,196 62,196" fill="var(--orange)"/>
      </svg>
      <div class="slide-title">About Our Company</div>
      <div class="brand"><span class="dot"></span>Bold Ledger</div>
      <div class="abs copy" style="left:9px;top:54px;width:118px">
        <p class="lead">Lorem ipsum dolor sit amet, consectetuer adipiscing elit, sed diam nonummy nibh euismod tincidunt ut laoreet dolore magna aliquam erat volutpat.</p>
        <p>Duis autem vel eum iriure dolor in hendrerit in vulputate velit esse molestie consequat, vel illum dolore eu feugiat nulla facilisis at vero eros et accumsan et iusto odio dignissim qui blandit praesent luptatum zzril delenit augue duis dolore te feugait nulla facilisi. Nam liber tempor cum soluta nobis eleifend option congue nihil imperdiet doming id quod mazim placerat facer possim assum.</p>
        <p>Typi non habent claritatem insitam est usus legentis in iis qui facit eorum claritatem.</p>
      </div>
      <div class="abs copy" style="left:136px;top:54px;width:116px">
        <p>Duis autem vel eum iriure dolor in hendrerit in vulputate velit esse molestie consequat, vel illum dolore eu feugiat nulla facilisis at vero eros et accumsan et iusto odio dignissim qui blandit praesent luptatum zzril delenit augue duis dolore te feugait nulla facilisi. Nam liber tempor cum soluta nobis eleifend option congue nihil imperdiet doming id quod mazim placerat facer possim assum.</p>
      </div>
      <div class="abs placeholder" style="left:136px;top:96px;width:112px;height:70px"></div>
      <div class="footer-url">www.boldledger.net | Page 1</div>
    </div>
  </section>

  <!-- 4 title + bullets -->
  <section class="cell">
    <div class="page-label">Page 4</div>
    <div class="slide">
      <svg class="frame" viewBox="0 0 262 196" width="262" height="196">
        <rect x="0" y="13" width="262" height="22" fill="var(--orange)"/>
        <polygon points="196,10 262,10 262,35 180,35" fill="var(--dark)"/>
        <rect x="0" y="35" width="186" height="1" fill="var(--dark)"/>
        <rect x="0" y="186" width="262" height="10" fill="var(--light)"/>
        <polygon points="70,188 262,188 262,196 62,196" fill="var(--orange)"/>
      </svg>
      <div class="slide-title">Title Goes Here</div>
      <div class="brand"><span class="dot"></span>Bold Ledger</div>
      <div class="abs placeholder" style="left:16px;top:50px;width:108px;height:68px"></div>
      <div class="abs copy" style="left:16px;top:126px;width:108px">
        <p>Duis autem vel eum iriure dolor in hendrerit in vulputate velit esse molestie consequat, vel illum dolore eu feugiat nulla facilisis at vero eros et accumsan et iusto odio dignissim qui blandit praesent luptatum zzril delenit augue duis dolore te feugait nulla facilisi.</p>
      </div>
      <ul class="abs bullets" style="left:140px;top:58px;width:108px">
        <li>Souvlaki ignitus carborundum e pluribus unum.</li>
        <li>Defacto lingo est igpay atinlay. Marquee selectus non provisio.</li>
        <li>Quote meon an estimate et non interruptus stadium.</li>
        <li>Sic tempus fugit esperanto hiccup estrogen.</li>
        <li>Epsum factorial non deposit quid pro quo hic escorol.</li>
      </ul>
      <div class="footer-url">www.boldledger.net | Page 2</div>
    </div>
  </section>

  <!-- 5 three columns -->
  <section class="cell">
    <div class="page-label">Page 5</div>
    <div class="slide">
      <svg class="frame" viewBox="0 0 262 196" width="262" height="196">
        <rect x="0" y="13" width="262" height="22" fill="var(--orange)"/>
        <polygon points="196,10 262,10 262,35 180,35" fill="var(--dark)"/>
        <rect x="0" y="35" width="186" height="1" fill="var(--dark)"/>
        <rect x="0" y="186" width="262" height="10" fill="var(--light)"/>
        <polygon points="70,188 262,188 262,196 62,196" fill="var(--orange)"/>
      </svg>
      <div class="slide-title">About Our Company</div>
      <div class="brand"><span class="dot"></span>Bold Ledger</div>
      <div class="trio">
        <div>
          <svg width="38" height="28" viewBox="0 0 38 28" aria-hidden="true">
            <rect x="6" y="2" width="26" height="18" fill="none" stroke="var(--dark)" stroke-width="1.8"/>
            <polyline points="10,16 16,10 20,13 27,6" fill="none" stroke="var(--dark)" stroke-width="1.3"/>
            <rect x="2" y="21" width="34" height="3" fill="var(--dark)"/>
          </svg>
          <div class="copy">Duis autem vel eum iriure dolor in hendrerit in vulputate velit esse molestie consequat, vel illum dolore eu feugiat nulla facilisis at vero eros et accumsan et iusto odio dignissim qui blandit praesent luptatum zzril delenit augue duis dolore te feugait nulla facilisi.</div>
        </div>
        <div>
          <svg width="38" height="28" viewBox="0 0 38 28" aria-hidden="true">
            <circle cx="14" cy="14" r="9" fill="none" stroke="var(--orange)" stroke-width="2"/>
            <circle cx="24" cy="14" r="9" fill="none" stroke="var(--orange)" stroke-width="2"/>
          </svg>
          <div class="copy">Duis autem vel eum iriure dolor in hendrerit in vulputate velit esse molestie consequat, vel illum dolore eu feugiat nulla facilisis at vero eros et accumsan et iusto odio dignissim qui blandit praesent luptatum zzril delenit augue duis dolore te feugait nulla facilisi.</div>
        </div>
        <div>
          <svg width="38" height="28" viewBox="0 0 38 28" aria-hidden="true">
            <polyline points="9,14 16,21 29,6" fill="none" stroke="var(--dark)" stroke-width="3" stroke-linecap="round" stroke-linejoin="round"/>
          </svg>
          <div class="copy">Duis autem vel eum iriure dolor in hendrerit in vulputate velit esse molestie consequat, vel illum dolore eu feugiat nulla facilisis at vero eros et accumsan et iusto odio dignissim qui blandit praesent luptatum zzril delenit augue duis dolore te feugait nulla facilisi.</div>
        </div>
      </div>
      <div class="footer-url">www.boldledger.net | Page 3</div>
    </div>
  </section>

  <!-- 6 bar chart -->
  <section class="cell">
    <div class="page-label">Page 6</div>
    <div class="slide">
      <svg class="frame" viewBox="0 0 262 196" width="262" height="196">
        <rect x="0" y="13" width="262" height="22" fill="var(--orange)"/>
        <polygon points="196,10 262,10 262,35 180,35" fill="var(--dark)"/>
        <rect x="0" y="35" width="186" height="1" fill="var(--dark)"/>
        <rect x="0" y="186" width="262" height="10" fill="var(--light)"/>
        <polygon points="70,188 262,188 262,196 62,196" fill="var(--orange)"/>
      </svg>
      <div class="slide-title">About Our Company</div>
      <div class="brand"><span class="dot"></span>Bold Ledger</div>
      <svg class="chart" width="246" height="86" viewBox="0 0 246 86" role="img" aria-label="Bar chart of three series across three categories">
        <g>
          <text x="4" y="7">5</text><text x="4" y="20">4</text><text x="4" y="33">3</text>
          <text x="4" y="46">2</text><text x="4" y="59">1</text><text x="4" y="72">0</text>
          <line x1="12" y1="71" x2="220" y2="71" stroke="#bdbdbd" stroke-width=".5"/>
        </g>
        <g>
          <rect x="26" y="15" width="12" height="56" fill="var(--orange)"/>
          <rect x="38" y="26" width="12" height="45" fill="var(--dark)"/>
          <rect x="50" y="19" width="12" height="52" fill="var(--mid)"/>
          <rect x="96" y="26" width="12" height="45" fill="var(--orange)"/>
          <rect x="108" y="14" width="12" height="57" fill="var(--dark)"/>
          <rect x="120" y="26" width="12" height="45" fill="var(--mid)"/>
          <rect x="164" y="30" width="12" height="41" fill="var(--orange)"/>
          <rect x="176" y="15" width="12" height="56" fill="var(--dark)"/>
          <rect x="188" y="12" width="12" height="59" fill="var(--mid)"/>
        </g>
        <text x="32" y="80">Category 1</text><text x="102" y="80">Category 2</text><text x="170" y="80">Category 3</text>
        <rect x="224" y="3" width="3" height="3" fill="var(--orange)"/><text x="229" y="6">Series 1</text>
        <rect x="224" y="10" width="3" height="3" fill="var(--dark)"/><text x="229" y="13">Series 2</text>
        <rect x="224" y="17" width="3" height="3" fill="var(--mid)"/><text x="229" y="20">Series 3</text>
      </svg>
      <div class="abs copy" style="left:16px;top:140px;width:230px">
        <p>Duis autem vel eum iriure dolor in hendrerit in vulputate velit esse molestie consequat, vel illum dolore eu feugiat nulla facilisis at vero eros et accumsan et iusto odio dignissim qui blandit praesent luptatum zzril delenit augue duis dolore te feugait nulla facilisi. Nam liber tempor cum soluta nobis eleifend option congue nihil imperdiet doming id quod mazim placerat facer possim assum.</p>
      </div>
      <div class="footer-url">www.boldledger.net | Page 4</div>
    </div>
  </section>

  <!-- 7 area chart -->
  <section class="cell">
    <div class="page-label">Page 7</div>
    <div class="slide">
      <svg class="frame" viewBox="0 0 262 196" width="262" height="196">
        <rect x="0" y="13" width="262" height="22" fill="var(--orange)"/>
        <polygon points="196,10 262,10 262,35 180,35" fill="var(--dark)"/>
        <rect x="0" y="35" width="186" height="1" fill="var(--dark)"/>
        <rect x="0" y="186" width="262" height="10" fill="var(--light)"/>
        <polygon points="70,188 262,188 262,196 62,196" fill="var(--orange)"/>
      </svg>
      <div class="slide-title">About Our Company</div>
      <div class="brand"><span class="dot"></span>Bold Ledger</div>
      <svg class="chart" width="246" height="86" viewBox="0 0 246 86" role="img" aria-label="Area chart of three series across three categories">
        <text x="4" y="7">5</text><text x="4" y="19">4</text><text x="4" y="31">3</text>
        <text x="4" y="43">2</text><text x="4" y="55">1</text><text x="4" y="67">0</text>
        <polygon points="14,66 14,45 60,17 120,20 212,13 212,66" fill="var(--dark)"/>
        <polygon points="14,66 14,45 60,21 120,35 160,30 212,29 212,66" fill="var(--orange)"/>
        <polygon points="14,66 14,45 80,38 140,31 212,22 212,66" fill="#9e9e9e"/>
        <line x1="12" y1="66" x2="214" y2="66" stroke="#bdbdbd" stroke-width=".5"/>
        <text x="14" y="74">Category 1</text><text x="106" y="74">Category 2</text><text x="192" y="74">Category 3</text>
        <rect x="222" y="3" width="3" height="3" fill="#9e9e9e"/><text x="227" y="6">Series 1</text>
        <rect x="222" y="10" width="3" height="3" fill="var(--orange)"/><text x="227" y="13">Series 2</text>
        <rect x="222" y="17" width="3" height="3" fill="var(--dark)"/><text x="227" y="20">Series 3</text>
      </svg>
      <div class="abs copy" style="left:14px;top:136px;width:234px">
        <p>Duis autem vel eum iriure dolor in hendrerit in vulputate velit esse molestie consequat, vel illum dolore eu feugiat nulla facilisis at vero eros et accumsan et iusto odio dignissim qui blandit praesent luptatum zzril delenit augue duis dolore te feugait nulla facilisi. Nam liber tempor cum soluta nobis eleifend option congue nihil imperdiet doming id quod mazim placerat facer possim assum.</p>
      </div>
      <div class="footer-url">www.boldledger.net | Page 5</div>
    </div>
  </section>

  <!-- 8 donut -->
  <section class="cell">
    <div class="page-label">Page 8</div>
    <div class="slide">
      <svg class="frame" viewBox="0 0 262 196" width="262" height="196">
        <rect x="0" y="13" width="262" height="22" fill="var(--orange)"/>
        <polygon points="196,10 262,10 262,35 180,35" fill="var(--dark)"/>
        <rect x="0" y="35" width="186" height="1" fill="var(--dark)"/>
        <rect x="0" y="186" width="262" height="10" fill="var(--light)"/>
        <polygon points="70,188 262,188 262,196 62,196" fill="var(--orange)"/>
        <g fill="none" stroke="#9a9a9a" stroke-width=".5">
          <polyline points="20,70 96,70 116,98"/>
          <polyline points="20,134 96,134 112,118"/>
          <polyline points="244,70 168,70 150,98"/>
          <polyline points="244,134 168,134 152,118"/>
        </g>
        <path d="M131,80 A28,28 0 0 1 159,108 L147,108 A16,16 0 0 0 131,92 Z" fill="var(--orange)"/>
        <path d="M159,108 A28,28 0 0 1 131,136 L131,124 A16,16 0 0 0 147,108 Z" fill="#c4c4c4"/>
        <path d="M131,136 A28,28 0 0 1 103,108 L115,108 A16,16 0 0 0 131,124 Z" fill="var(--dark)"/>
        <path d="M103,108 A28,28 0 0 1 131,80 L131,92 A16,16 0 0 0 115,108 Z" fill="#4a4a4a"/>
        <g font-family="Lato,sans-serif" font-size="4.2" fill="#ffffff">
          <text x="116" y="100">25%</text><text x="138" y="100">25%</text>
          <text x="116" y="120">25%</text><text x="138" y="120">25%</text>
        </g>
      </svg>
      <div class="slide-title">About Our Company</div>
      <div class="brand"><span class="dot"></span>Bold Ledger</div>
      <div class="note" style="left:22px;top:59px"><h4>NOBIS VIDENTUR</h4><div class="copy">Lorem ipsum dolor sit amet, consectetuer adipiscing elit, sed diam nonummy nibh euismod tincidunt.</div></div>
      <div class="note" style="left:22px;top:123px"><h4>NOBIS VIDENTUR</h4><div class="copy">Lorem ipsum dolor sit amet, consectetuer adipiscing elit, sed diam nonummy nibh euismod tincidunt.</div></div>
      <div class="note hot" style="left:172px;top:59px"><h4>NOBIS VIDENTUR</h4><div class="copy">Lorem ipsum dolor sit amet, consectetuer adipiscing elit, sed diam nonummy nibh euismod tincidunt.</div></div>
      <div class="note pale" style="left:176px;top:123px"><h4>NOBIS VIDENTUR</h4><div class="copy">Lorem ipsum dolor sit amet, consectetuer adipiscing elit, sed diam nonummy nibh euismod tincidunt.</div></div>
      <div class="footer-url">www.boldledger.net | Page 6</div>
    </div>
  </section>

  <!-- 9 table -->
  <section class="cell">
    <div class="page-label">Page 9</div>
    <div class="slide">
      <svg class="frame" viewBox="0 0 262 196" width="262" height="196">
        <rect x="0" y="13" width="262" height="22" fill="var(--orange)"/>
        <polygon points="196,10 262,10 262,35 180,35" fill="var(--dark)"/>
        <rect x="0" y="35" width="186" height="1" fill="var(--dark)"/>
        <rect x="0" y="186" width="262" height="10" fill="var(--light)"/>
        <polygon points="70,188 262,188 262,196 62,196" fill="var(--orange)"/>
        <line x1="14" y1="58" x2="250" y2="58" stroke="#cfcfcf" stroke-width=".5"/>
      </svg>
      <div class="slide-title">About Our Company</div>
      <div class="brand"><span class="dot"></span>Bold Ledger</div>
      <table class="grid-table">
        <thead><tr><th></th><th>A</th><th>B</th><th>C</th></tr></thead>
        <tbody>
          <tr class="band"><td>Type 1</td><td>20</td><td>30</td><td>40</td></tr>
          <tr><td>Type 2</td><td>50</td><td>60</td><td>70</td></tr>
          <tr class="band"><td>Type 3</td><td>80</td><td>90</td><td>100</td></tr>
        </tbody>
      </table>
      <div class="footer-url">www.boldledger.net | Page 7</div>
    </div>
  </section>

  <!-- 10 team -->
  <section class="cell">
    <div class="page-label">Page 10</div>
    <div class="slide">
      <svg class="frame" viewBox="0 0 262 196" width="262" height="196">
        <rect x="0" y="13" width="262" height="22" fill="var(--orange)"/>
        <polygon points="196,10 262,10 262,35 180,35" fill="var(--dark)"/>
        <rect x="0" y="35" width="186" height="1" fill="var(--dark)"/>
        <rect x="0" y="186" width="262" height="10" fill="var(--light)"/>
        <polygon points="70,188 262,188 262,196 62,196" fill="var(--orange)"/>
      </svg>
      <div class="slide-title">About Our Company</div>
      <div class="brand"><span class="dot"></span>Bold Ledger</div>
      <div class="team">
        <div>
          <div class="portrait" role="img" aria-label="Portrait photo of team member"></div>
          <div class="person-name">Mr J. Carter</div><div class="person-role">(President)</div>
          <div class="copy">Lorem ipsum dolor sit amet, consectetuer adipiscing elit, sed diam nonummy nibh euismod tincidunt ut laoreet dolore magna aliquam erat volutpat.</div>
        </div>
        <div>
          <div class="portrait" role="img" aria-label="Portrait photo of team member" style="background:linear-gradient(135deg,#e6e6e6,#8e959c)"></div>
          <div class="person-name">Mr J. Carter</div><div class="person-role">(President)</div>
          <div class="copy">Lorem ipsum dolor sit amet, consectetuer adipiscing elit, sed diam nonummy nibh euismod tincidunt ut laoreet dolore magna aliquam erat volutpat.</div>
        </div>
        <div>
          <div class="portrait" role="img" aria-label="Portrait photo of team member outdoors" style="background:linear-gradient(135deg,#a8a07a,#c9b9a2)"></div>
          <div class="person-name">Mr J. Carter</div><div class="person-role">(President)</div>
          <div class="copy">Lorem ipsum dolor sit amet, consectetuer adipiscing elit, sed diam nonummy nibh euismod tincidunt ut laoreet dolore magna aliquam erat volutpat.</div>
        </div>
      </div>
      <div class="footer-url">www.boldledger.net | Page 8</div>
    </div>
  </section>

  <!-- 11 stats -->
  <section class="cell">
    <div class="page-label">Page 11</div>
    <div class="slide">
      <svg class="frame" viewBox="0 0 262 196" width="262" height="196">
        <rect x="0" y="13" width="262" height="22" fill="var(--orange)"/>
        <polygon points="196,10 262,10 262,35 180,35" fill="var(--dark)"/>
        <rect x="0" y="35" width="186" height="1" fill="var(--dark)"/>
        <rect x="0" y="186" width="262" height="10" fill="var(--light)"/>
        <polygon points="70,188 262,188 262,196 62,196" fill="var(--orange)"/>
      </svg>
      <div class="slide-title">About Our Company</div>
      <div class="brand"><span class="dot"></span>Bold Ledger</div>
      <div class="stat orange" style="left:29px;top:53px">
        <div class="badge"><svg width="11" height="9" viewBox="0 0 11 9"><polygon points="1,3 5,3 10,0 10,9 5,6 1,6" fill="#fff"/></svg></div>
        <div class="figure">915,456,459</div>
        <div class="copy">Lorem ipsum dolor sit amet, consectetuer adipiscing elit, sed diam nonummy nibh euismod tincidunt.</div>
      </div>
      <div class="stat dark" style="left:153px;top:53px">
        <div class="badge"><svg width="10" height="11" viewBox="0 0 10 11"><circle cx="5" cy="6.5" r="4" fill="none" stroke="#fff" stroke-width="1.2"/><rect x="3.5" y="0.5" width="3" height="2" fill="#fff"/></svg></div>
        <div class="figure">111,458,564</div>
        <div class="copy">Lorem ipsum dolor sit amet, consectetuer adipiscing elit, sed diam nonummy nibh euismod tincidunt.</div>
      </div>
      <div class="stat dark" style="left:29px;top:118px">
        <div class="badge"><svg width="11" height="9" viewBox="0 0 11 9"><ellipse cx="5.5" cy="5" rx="5" ry="3.5" fill="#fff"/></svg></div>
        <div class="figure">100%</div>
        <div class="copy">Lorem ipsum dolor sit amet, consectetuer adipiscing elit, sed diam nonummy nibh euismod tincidunt.</div>
      </div>
      <div class="stat grey" style="left:153px;top:118px">
        <div class="badge"><svg width="10" height="10" viewBox="0 0 10 10"><rect x="1" y="6" width="2" height="4" fill="#fff"/><rect x="4" y="3" width="2" height="7" fill="#fff"/><rect x="7" y="0" width="2" height="10" fill="#fff"/></svg></div>
        <div class="figure">100%</div>
        <div class="copy">Lorem ipsum dolor sit amet, consectetuer adipiscing elit, sed diam nonummy nibh euismod tincidunt.</div>
      </div>
      <div class="footer-url">www.boldledger.net | Page 9</div>
    </div>
  </section>

  <!-- 12 closing -->
  <section class="cell">
    <div class="page-label">Page 12</div>
    <div class="slide closing">
      <svg class="frame" viewBox="0 0 262 196" width="262" height="196">
        <polygon points="0,130 0,196 120,196 184,132 60,132 0,174" fill="#f4f4f4"/>
        <polygon points="0,150 0,196 10,196 72,140 60,140" fill="var(--dark)"/>
        <polygon points="20,196 60,196 166,110 140,110" fill="var(--dark)"/>
        <polygon points="70,196 262,196 262,100 190,100" fill="#f4f4f4"/>
        <polygon points="230,40 262,14 262,4 220,40" fill="#e5530f"/>
        <polygon points="248,10 262,0 262,6" fill="var(--dark)"/>
      </svg>
      <div class="thanks">THANK<br>&nbsp;&nbsp;YOU</div>
      <div class="site">www.boldledger.net</div>
      <div class="brand-big"><span class="dot"></span>Bold Ledger</div>
    </div>
  </section>

</main>
</body>
</html>
```